Real Estate Company Looking for Business Card Designs for 3 Executives

Hello!
Thanks so much for considering our project! We are a real estate investment company located in Edmonton, Alberta called Bellhaven Group of Companies. We invest/develop both commercial and residential real estate and are looking to create 3 DOUBLE-SIDED business cards for 3 top executives in the company! (for some reason it won't let us select the double-sided option, but yes, the cards are double sided and would be happy to tip extra)

We have certain guidelines that we want our business cards to for sure follow - the back of the Business card has to be the Black Background Version of the Logo which has already been designed and linked as a file (first file). We want the entire back of the card to simply just be the black background logo. In terms of the front of the card, would like to see a smaller version of the white background logo (linked as the second file) in the top left hand corner - of course, feel free to get creative and we can make revisions together along the way! and Then after that, just text. We want the card to be sharp, clean, easy on the eyes and highly professional looking. We would like the card to include the Full name of the Company (Bellhaven Group of Companies), Name of the Person, Title, Phone, Email. If possible please provide the front part of the card for 3 people:

1) Bellhaven Group of Companies, Liora Quenby, Chief Financial Officer, 780-555-0142, lioraquenby@bellhavengroup.example

2) Bellhaven Group of Companies, Tobias Quenby, Chief Executive Officer, 780-555-0187, tobiasquenby@bellhavengroup.example

3) Bellhaven Group of Companies, Rui Delcourt, Chief Operations Officer, 587-555-0163, ruidelcourt@bellhavengroup.example

Thank you so much for considering our project & we look forward to seeing your designs!

```html
<!DOCTYPE html>
<html lang="en">
<head>
<meta charset="utf-8">
<title>Bellhaven Group of Companies — Business Card</title>
<link href="https://fonts.googleapis.com/css2?family=Arimo:wght@400&family=Libre+Baskerville:wght@700&display=swap" rel="stylesheet">
<style>
  :root {
    --stage: #d4d4d4;
    --card-white: #ffffff;
    --card-black: #1e1e1e;
    --ink: #1a1a1a;
    --ink-soft: #333333;
    --rule: #3a3a3a;
    --on-dark: #ffffff;
  }
  * { box-sizing: border-box; margin: 0; padding: 0; }
  html, body {
    width: 1200px; height: 788px; overflow: hidden;
    background: var(--stage);
  }
  .stage {
    position: relative; width: 1200px; height: 788px;
    display: flex; align-items: center; justify-content: center; gap: 40px;
  }
  .card {
    width: 520px; height: 298px; border-radius: 22px;
    position: relative; overflow: hidden;
    box-shadow: 0 6px 18px rgba(0,0,0,0.18);
  }
  .card--front { background: var(--card-white); color: var(--ink); }
  .card--back {
    background: var(--card-black); color: var(--on-dark);
    display: flex; align-items: center; justify-content: center;
  }

  .wordmark {
    font-family: "Arimo", Arial, sans-serif;
    font-weight: 400;
    text-transform: uppercase;
    letter-spacing: 0.28em;
    white-space: nowrap;
  }
  .card--front .wordmark {
    position: absolute; left: 44px; top: 46px;
    font-size: 13px; color: var(--ink);
    padding-bottom: 8px; border-bottom: 1px solid var(--rule);
  }
  .card--back .wordmark {
    font-size: 20px; color: var(--on-dark);
    padding-bottom: 12px; border-bottom: 1px solid var(--on-dark);
  }

  .person { position: absolute; left: 44px; top: 112px; }
  .person__name {
    font-family: "Libre Baskerville", Georgia, serif;
    font-weight: 700; font-size: 21px; color: var(--ink);
  }
  .person__title {
    font-family: "Arimo", Arial, sans-serif;
    font-size: 14px; color: var(--ink-soft); margin-top: 4px;
  }
  .person__divider {
    width: 14px; height: 1px; background: var(--rule); margin-top: 12px;
  }

  .contacts {
    position: absolute; left: 44px; top: 190px;
    list-style: none;
    font-family: "Arimo", Arial, sans-serif; font-size: 14px; color: var(--ink);
  }
  .contacts li { display: flex; align-items: center; gap: 8px; height: 24px; }
  .contacts svg { width: 12px; height: 12px; flex: none; fill: var(--ink); }
</style>
</head>
<body>
<main class="stage">
  <section class="card card--front" aria-label="Card front">
    <div class="wordmark">Bellhaven Group of Companies</div>
    <div class="person">
      <h1 class="person__name">Tobias Quenby</h1>
      <p class="person__title">Chief Executive Officer</p>
      <div class="person__divider"></div>
    </div>
    <ul class="contacts">
      <li>
        <svg viewBox="0 0 12 12" aria-hidden="true"><circle cx="6" cy="6" r="6"/><path d="M3.6 3.2c.3-.3.7-.3.9 0l.6.8c.2.3.1.6-.1.8l-.3.3c.3.7.9 1.3 1.6 1.6l.3-.3c.2-.2.5-.3.8-.1l.8.6c.3.2.3.6 0 .9l-.4.4C6.6 8.6 3.4 5.4 3.2 3.6z" fill="#fff"/></svg>
        <span>780-555-0187</span>
      </li>
      <li>
        <svg viewBox="0 0 12 12" aria-hidden="true"><rect x="0" y="2" width="12" height="8" rx="1"/><path d="M0.8 2.8 6 6.8l5.2-4" stroke="#fff" stroke-width="1" fill="none"/></svg>
        <span>tobiasquenby@bellhavengroup.example</span>
      </li>
      <li>
        <svg viewBox="0 0 12 12" aria-hidden="true"><circle cx="6" cy="6" r="6"/><path d="M1 6h10M6 1c-2 2.7-2 7.3 0 10M6 1c2 2.7 2 7.3 0 10" stroke="#fff" stroke-width="0.8" fill="none"/></svg>
        <span>www.bellhavengroup.example</span>
      </li>
    </ul>
  </section>

  <section class="card card--back" aria-label="Card back">
    <div class="wordmark">Bellhaven Group of Companies</div>
  </section>
</main>
</body>
</html>
```